Jewelers Website

This is for the DESIGN ONLY.
I am a software programmer and will be doing the development.
New website design for
www.lunacrestgems.com.au
Need a fresh new look for an online only jewellery business who produce their jewellery by hand. I would like it designed in a parallax style. Feel free to recommend fonts to use for the site. This is an Australian based company located in NSW so shots of sites in NSW might make nice background images.
http://vornaplex.me/demo/#theme=parallax
To contain the below sections
About Us
Contact Us
Gallery
Testimonials
Diamond Types
The colour scheme is to be Black / White and Silver.
With the Parallax style there will be moving sections and images for added impact.
Target Market(s)
Young Adults mainly engagement jewellery

```html
<!DOCTYPE html>
<html lang="en">
<head>
<meta charset="utf-8">
<title>Lunacrest Gems</title>
<link rel="stylesheet" href="https://fonts.googleapis.com/css2?family=Montserrat:wght@700&family=Lato:wght@300;400;700&display=swap">
<style>
:root{
  --ink:#0b0b0d;
  --panel:#121215;
  --panel-2:#1a1a1f;
  --slate:#23252c;
  --white:#ffffff;
  --silver:#c9c9cf;
  --muted:#9a9aa2;
  --accent:#d3203c;
  --cyan:#16c4e6;
  --field:#e4e4e6;
  --field-text:#a3a3a8;
  --footer:#060607;
  --social:#3a3f4a;
}
*{margin:0;padding:0;box-sizing:border-box}
html,body{width:1200px;height:4018px;overflow:hidden;background:var(--ink)}
body{position:relative;font-family:"Lato",sans-serif;color:var(--white)}
.abs{position:absolute}
.photo{position:absolute}

/* nav */
.site-nav{position:absolute;left:0;top:0;width:1200px;height:94px;z-index:10;background:rgba(10,10,12,.55)}
.brand{position:absolute;left:80px;top:0;width:199px;height:88px;background:#1f1f22;display:flex;align-items:center;justify-content:center;gap:10px}
.brand-mark{width:14px;height:14px;background:var(--white)}
.brand-name{font-size:22px;font-weight:400;letter-spacing:1px;line-height:1.05;text-transform:uppercase;color:var(--white)}
.menu{position:absolute;top:31px;left:0;list-style:none;font-size:15px;font-weight:700}
.menu li{position:absolute;white-space:nowrap}
.menu .active{border:1px solid var(--white);padding:4px 18px;top:-5px}

/* hero */
.hero{position:absolute;left:0;top:0;width:1200px;height:897px;background:linear-gradient(135deg,#3a4150,#1d2129 60%,#2a3240);overflow:hidden}
.hero-title{position:absolute;left:595px;top:222px;font-family:"Montserrat",sans-serif;font-weight:700;font-size:45px;line-height:62px;letter-spacing:3px;text-transform:uppercase}
.dots{position:absolute;display:flex;gap:8px}
.dots span{width:13px;height:13px;border-radius:50%;background:var(--white)}
.dots span.on{background:var(--accent)}
.hero-brand{position:absolute;left:10px;top:770px;width:220px;text-align:center;z-index:5}
.hero-brand .sq{width:110px;height:110px;margin:0 auto 26px;background:var(--white);transform:rotate(45deg) scale(.72)}
.hero-brand p{font-size:17px;letter-spacing:3px;text-transform:uppercase}

/* sections */
.section{position:absolute;left:0;width:1200px;overflow:hidden}
.section-title{position:absolute;display:flex;align-items:center;gap:20px;font-size:31px;font-weight:400;white-space:nowrap}
.section-title .icon{width:20px;height:20px;background:var(--white);transform:rotate(45deg)}
.copy{position:absolute;font-size:12.5px;line-height:19px;color:var(--silver)}
.copy p+p{margin-top:19px}
.btn{position:absolute;width:198px;height:38px;background:var(--white);color:#222;font-size:14px;display:flex;align-items:center;justify-content:center}

.about{top:897px;height:622px;background:linear-gradient(180deg,#101013,#0c0c0e)}
.gallery{top:1519px;height:651px;background:var(--panel)}
.testimonials{top:2170px;height:670px;background:var(--ink)}
.types{top:2840px;height:460px;background:#000}
.contact{top:3300px;height:585px;background:linear-gradient(90deg,#6b4a3a,#c7a58a 45%,#8a6e5c 75%,#3d3029)}
.site-footer{position:absolute;left:0;top:3885px;width:1200px;height:133px;background:var(--footer)}

/* testimonial card */
.quote-card{position:absolute;left:354px;top:289px;width:846px;height:311px;background:linear-gradient(135deg,#2a2a2e,#1c1c20 50%,#2b2b30)}
.quote-name{position:absolute;left:375px;top:38px;font-size:30px}
.quote-role{position:absolute;left:375px;top:80px;font-size:14px;color:var(--silver)}
.quote-note{position:absolute;left:375px;top:98px;font-size:11px;color:#5fc35a}
.quote-text{position:absolute;left:375px;top:126px;width:400px;font-size:14.5px;line-height:20px;color:var(--silver)}

/* contact form */
.contact-head{position:absolute;left:0;width:1200px;text-align:center;color:#1a1a1a}
.form{position:absolute;left:335px;top:177px;width:562px;height:381px;background:var(--white)}
.field{position:absolute;left:29px;width:509px;background:var(--field);color:var(--field-text);font-size:13px;text-align:center;padding-top:11px}
.submit{position:absolute;left:228px;top:290px;width:117px;height:37px;background:var(--cyan);color:var(--white);font-size:14px;font-weight:700;display:flex;align-items:center;justify-content:center}

.social{position:absolute;top:14px;left:492px;display:flex;gap:14px}
.social span{width:44px;height:44px;display:block}
.social .boxed{background:var(--social)}
.social .plain{width:30px;height:30px;margin-top:7px;border-radius:50%;background:#d8d8dc}
.legal{position:absolute;top:86px;width:1200px;text-align:center;font-size:11px;color:var(--muted)}
</style>
</head>
<body>

<header class="hero">
  <div class="photo" role="img" aria-label="Portrait of a woman in a black hat, lace glove and pearl necklace" style="inset:0;clip-path:polygon(0 0,700px 0,700px 240px,600px 897px,0 520px);background:linear-gradient(160deg,#6d717c,#3e4350 45%,#c9b8aa 80%,#8c8e94)"></div>
  <div class="photo" role="img" aria-label="Portrait of a woman wearing a red gemstone ring" style="inset:0;clip-path:polygon(1200px 290px,1200px 897px,590px 897px);background:linear-gradient(135deg,#2a5562,#1b2f38 50%,#c98f7c 80%,#6a2024)"></div>
  <svg class="abs" style="left:0;top:0" width="1200" height="897" aria-hidden="true">
    <polygon points="0,522 362,897 0,897" fill="#0b0b0d"/>
    <polygon points="362,897 470,820 590,897" fill="#141418"/>
    <line x1="1200" y1="290" x2="590" y2="897" stroke="#0b0b0d" stroke-width="14"/>
  </svg>
  <h1 class="hero-title">Welcome<br>to the<br>Lunacrest<br>Gems</h1>
  <div class="dots" style="left:608px;top:483px"><span class="on"></span><span></span><span></span><span></span></div>
</header>

<nav class="site-nav">
  <div class="brand"><span class="brand-mark"></span><span class="brand-name">Lunacrest<br>Gems</span></div>
  <ul class="menu">
    <li class="active" style="left:530px">About Us</li>
    <li style="left:659px">Gallery</li>
    <li style="left:750px">Diamond Types</li>
    <li style="left:892px">Testimonials</li>
    <li style="left:1021px">Contact Us</li>
  </ul>
</nav>

<section class="section about">
  <svg class="abs" style="left:0;top:0" width="1200" height="622" aria-hidden="true">
    <polygon points="0,0 470,0 360,130" fill="#16161a"/>
    <polygon points="500,0 900,0 760,180" fill="#0e0e11"/>
  </svg>
  <div class="photo" role="img" aria-label="Smiling woman wearing diamond earrings and necklace" style="left:817px;top:14px;width:383px;height:608px;clip-path:polygon(150px 0,383px 0,383px 608px,0 608px,60px 330px);background:linear-gradient(150deg,#3a2a24,#c69a80 45%,#e4c4ad 70%,#2c2222)"></div>
  <h2 class="section-title" style="left:102px;top:232px"><span class="icon"></span>About Lunacrest Gems</h2>
  <div class="copy" style="left:102px;top:296px;width:540px">
    <p>Lorem ipsum dolor sit amet, consectetur adipisicing elit, sed do eiusmod tempor incididunt ut labore et dolore magna aliqua sit amet, consectetur adipisicing elit, sed do eiusmod tempor incididunt ut labore et dolore lorem ipsum dolor sit amet, consectetur adipisicing elit, sed do eiusmod tempor incididunt ut labore et dolore sit amet eiusmod tempor</p>
    <p>incididunt ut labore et dolore lorem ipsum dolor sit amet, consectetur adipisicing elit, sed do eiusmod tempor incididunt ut labore et dolore sit amet adipisicing elit, sed do eiusmod tempor incididunt ut labore et</p>
  </div>
  <div class="btn" style="left:102px;top:523px">Read More</div>
</section>

<div class="hero-brand">
  <div class="sq"></div>
  <p>Lunacrest Gems</p>
</div>

<section class="section gallery">
  <div class="photo" role="img" aria-label="Woman with long curls wearing a layered necklace" style="left:0;top:0;width:737px;height:651px;clip-path:polygon(0 0,600px 0,737px 330px,737px 651px,0 651px);background:linear-gradient(120deg,#2b2b34,#5a4a44 40%,#b58a70 60%,#2a2a30)"></div>
  <svg class="abs" style="left:0;top:0" width="1200" height="651" aria-hidden="true">
    <polygon points="960,0 1200,0 1200,120" fill="#0d0d10"/>
  </svg>
  <h2 class="section-title" style="left:729px;top:78px"><span class="icon"></span>Our Gallery</h2>
  <div class="copy" style="left:742px;top:124px;width:330px">
    <p>Lorem ipsum dolor sit amet, consectetur adipisicing elit, sed do eiusmod tempor incididunt ut labore et lorem ipsum dolor sit amet, consectetur adipisicing elit, sed do eiusmod tempor incididunt ut labore et dolore lorem ipsum dolor sit amet, consectetur adipisicing elit, sed do eiusmod tempor</p>
    <p>incididunt ut labore et dolore sit amet, consectetur adipisicing elit, sed od tempor incididunt ut labore et lorem ipsum dolor sit amet, consectetur adipi-</p>
  </div>
  <div class="photo" role="img" aria-label="Woman wearing a diamond pendant" style="left:660px;top:480px;width:180px;height:180px;transform:rotate(45deg);background:linear-gradient(135deg,#d8c4b4,#8a7060)"></div>
  <div class="photo" role="img" aria-label="Woman with hand raised, wearing a bracelet" style="left:870px;top:470px;width:180px;height:180px;transform:rotate(45deg);background:linear-gradient(135deg,#cfd6dc,#6d6a70)"></div>
  <div class="photo" role="img" aria-label="Woman wearing statement earrings" style="left:1060px;top:470px;width:160px;height:160px;transform:rotate(45deg);background:linear-gradient(135deg,#bfb4b0,#3a2c2c)"></div>
</section>

<section class="section testimonials">
  <svg class="abs" style="left:0;top:0" width="1200" height="670" aria-hidden="true">
    <polygon points="560,0 1200,0 1200,289 850,289" fill="#141417"/>
    <polygon points="0,420 354,289 354,670 0,670" fill="#060607"/>
  </svg>
  <h2 class="section-title" style="left:102px;top:72px"><span class="icon"></span>Testimonials</h2>
  <div class="copy" style="left:110px;top:122px;width:420px">
    <p>Lorem ipsum dolor sit amet, consectetur adipisicing elit, sed do eiusmod tempor incididunt ut labore et lorem ipsum dolor sit amet, consectetur adipisicing elit, sed do eiusmod tempor incididunt ut labore et lorem ipsum dolor sit amet, consectetur adipisicing elit, sed do eiusmod tempor incididunt ut labore et dolore lorem ipsum dolor sit amet, consectetur adipisicing elit, sed do eiusmod tempor</p>
  </div>
  <div class="quote-card">
    <svg class="abs" style="left:0;top:0" width="846" height="311" aria-hidden="true">
      <polygon points="0,0 200,0 0,190" fill="var(--accent)"/>
      <polygon points="0,0 100,0 0,95" fill="#3a3a3f"/>
      <path d="M122 110 Q95 155 122 200" fill="none" stroke="#8a8a90" stroke-width="2"/>
      <path d="M724 110 Q751 155 724 200" fill="none" stroke="#8a8a90" stroke-width="2"/>
    </svg>
    <div class="photo" role="img" aria-label="Client portrait" style="left:166px;top:92px;width:160px;height:160px;border-radius:50%;background:linear-gradient(135deg,#a7c3d8,#d9a88a 60%,#7a4a3a)"></div>
    <div class="quote-name">Mirela Tovan</div>
    <div class="quote-role">Accountant Manager</div>
    <div class="quote-note">client since 2014</div>
    <p class="quote-text">Lorem ipsum dolor sit amet, consectetur adipisicing elit, sed do eiusmod tempor incididunt ut labore et dolore magna aliqua. Ut enim ad minim veniam, quis nostrud exercitation</p>
    <div class="dots" style="left:219px;top:287px"><span></span><span></span><span></span></div>
  </div>
</section>

<section class="section types">
  <h2 class="section-title" style="left:102px;top:64px"><span class="icon"></span>Our Diamond Types</h2>
  <div class="copy" style="left:110px;top:108px;width:290px">
    <p>Lorem ipsum dolor sit amet, consectetur adipisicing elit, sed do eiusmod tempor incididunt ut labore et lorem ipsum dolor sit amet, consectetur adipisicing elit, sed do eiusmod tempor incididunt ut labore</p>
  </div>
  <div class="btn" style="left:102px;top:227px">Read More</div>
  <div class="photo" role="img" aria-label="Large cut diamond" style="left:385px;top:105px;width:230px;height:230px;transform:rotate(45deg);background:linear-gradient(135deg,#f2f2f2,#8c8c8c 55%,#d6d6d6)"></div>
  <div class="photo" role="img" aria-label="Blue-tinted diamond" style="left:705px;top:148px;width:120px;height:120px;transform:rotate(45deg);background:linear-gradient(135deg,#bfe6f2,#4e8ba0)"></div>
  <div class="photo" role="img" aria-label="Scattered diamonds" style="left:625px;top:250px;width:130px;height:130px;transform:rotate(45deg);background:linear-gradient(135deg,#e5e5e5,#3c3c3c)"></div>
  <div class="photo" role="img" aria-label="Single brilliant diamond" style="left:842px;top:60px;width:120px;height:120px;transform:rotate(45deg);background:linear-gradient(135deg,#ffffff,#a0a0aa)"></div>
  <div class="photo" role="img" aria-label="Diamond on a dark surface" style="left:810px;top:235px;width:140px;height:140px;transform:rotate(45deg);background:linear-gradient(135deg,#e9e9ec,#55555c)"></div>
  <div class="photo" role="img" aria-label="Pile of small diamonds" style="left:942px;top:168px;width:110px;height:110px;transform:rotate(45deg);background:linear-gradient(135deg,#d8d8dc,#2c2c30)"></div>
</section>

<section class="section contact">
  <div class="photo" role="img" aria-label="Woman with long hair in soft warm light" style="left:0;top:0;width:360px;height:585px;background:linear-gradient(160deg,#4a2e22,#c79a7c 50%,#e8d2c2 75%,#7a5c50)"></div>
  <svg class="abs" style="left:0;top:0" width="1200" height="585" aria-hidden="true">
    <polygon points="1020,0 1200,0 1200,170" fill="#0b0b0d"/>
  </svg>
  <p class="contact-head" style="top:33px;font-size:27px">Contact Us</p>
  <h2 class="contact-head" style="top:69px;font-size:42px;font-weight:400">Get In touch With Us</h2>
  <p class="contact-head" style="top:129px;font-size:14px">Lorem ipsum dolor sit amet, consectetur adipisicing elit, sed do</p>
  <div class="form">
    <div class="field" style="top:46px;height:38px">Name</div>
    <div class="field" style="top:102px;height:38px">Email</div>
    <div class="field" style="top:158px;height:156px">Message</div>
    <div class="submit">SUBMIT</div>
  </div>
</section>

<footer class="site-footer">
  <div class="social">
    <span class="boxed"></span>
    <span class="plain"></span>
    <span class="plain"></span>
    <span class="plain"></span>
  </div>
  <p class="legal">© 2014 copy right &nbsp;|&nbsp; privacy policy</p>
</footer>

</body>
</html>
```